boosters

revamp current booster flyer - modernize make it look better

please use website
Kowhaibaygroup.co.nz for as much as possible

i want you all to come with own wording description etc

```html
<!DOCTYPE html>
<html lang="en">
<head>
<meta charset="utf-8">
<title>Kowhai Bay Group – Brake and Clutch Boosters</title>
<link rel="stylesheet" href="https://fonts.googleapis.com/css2?family=Bebas+Neue&family=Poppins:wght@500;600;700;800&display=swap">
<style>
:root{
  --yellow:#f7d600;
  --yellow-deep:#efc800;
  --black:#0b0b0b;
  --white:#ffffff;
  --light:#efefef;
  --grey-line:#bdbdbd;
  --stage:#dcdcdc;
}
*{margin:0;padding:0;box-sizing:border-box}
html,body{width:1200px;height:2348px;overflow:hidden;background:var(--stage)}
body{position:relative;font-family:"Poppins",sans-serif;color:var(--black)}
.flyer{position:absolute;left:48px;top:460px;width:960px;height:1242px;transform:scale(1.15);transform-origin:0 0;background:var(--light);overflow:hidden;box-shadow:0 18px 40px rgba(0,0,0,.35)}
.hero-art{position:absolute;left:0;top:0;width:960px;height:620px}
.abs{position:absolute}
.brand{left:0;width:960px;top:58px;text-align:center}
.brand-mark{display:block;width:58px;height:58px;margin:0 auto 14px;background:var(--yellow)}
.brand-name{font-weight:700;font-size:30px;color:var(--white);letter-spacing:1px}
.headline{left:0;width:960px;text-align:center;font-family:"Bebas Neue",sans-serif;line-height:1}
.headline-top{top:250px;font-size:70px;color:var(--yellow)}
.headline-main{top:310px;font-size:96px;color:var(--white)}
.product-hero{left:300px;top:418px;width:360px;height:146px;border-radius:40px 60px 30px 30px;background:radial-gradient(ellipse at 55% 45%,#e9e9e9,#a9a9a9 55%,#5a5a5a 90%)}
.range-title{left:142px;top:604px;width:680px;height:40px}
.range-title span{position:absolute;left:0;top:0;width:100%;text-align:center;font-weight:700;font-size:27px;line-height:40px;color:var(--yellow)}
.range-box{left:50px;top:627px;width:860px;height:190px;background:var(--yellow);border:2px solid var(--yellow-deep);border-radius:16px;box-shadow:0 8px 10px rgba(0,0,0,.25)}
.range-item{top:663px;width:140px;height:140px;border-radius:50%;border:3px solid var(--black);background:var(--white);display:flex;align-items:center;justify-content:center}
.range-photo{width:96px;height:70px;border-radius:20px;background:radial-gradient(ellipse at 50% 45%,#6a6a6a,#1b1b1b 70%)}
.company{left:50px;top:848px;font-weight:800;font-size:34px;line-height:40px}
.specialty{left:43px;top:892px;height:27px;padding:0 10px;background:var(--black);color:var(--white);border-radius:4px;font-weight:600;font-size:16px;line-height:27px}
.service{display:flex;align-items:center;gap:16px;font-weight:500;font-size:17px}
.service svg{width:52px;height:52px;flex:none}
.service-divider{height:1px;background:var(--grey-line)}
.note{left:54px;top:1068px;font-weight:500;font-size:17px}
.aim{left:619px;top:855px;width:286px;height:232px;background:var(--black);border-radius:18px}
.aim-band{left:610px;top:944px;width:305px;height:30px;background:var(--yellow);text-align:center;font-weight:700;font-size:23px;line-height:30px}
.aim-text{left:619px;top:986px;width:286px;text-align:center;color:var(--white);font-weight:600;font-size:20px;line-height:24px}
.footer-art{position:absolute;left:0;top:1114px;width:960px;height:128px}
.free-phone{left:52px;top:1132px;display:flex;height:26px;font-weight:600;font-size:19px;line-height:24px}
.free-label{background:var(--black);color:var(--white);padding:0 9px}
.free-number{background:var(--white);border:2px solid var(--black);padding:0 8px;line-height:22px}
.phones{left:52px;top:1166px;display:flex;gap:22px;font-weight:700;font-size:20px;align-items:center}
.phones span,.contact span{display:inline-flex;align-items:center;gap:8px}
.contact{font-weight:600;font-size:15.5px;display:flex;align-items:center;gap:8px}
.address{left:416px;top:1154px;width:250px;color:var(--white);font-weight:600;font-size:16px;line-height:20px;display:flex;gap:8px}
.unsubscribe{left:690px;top:1162px;width:218px;height:23px;background:var(--yellow);text-align:center;font-weight:600;font-size:15px;line-height:23px}
</style>
</head>
<body>
<main class="flyer">
  <svg class="hero-art" viewBox="0 0 960 620" aria-hidden="true">
    <defs>
      <linearGradient id="engineTone" x1="0" y1="0" x2="1" y2="1">
        <stop offset="0" stop-color="#2b2b2b"/><stop offset=".5" stop-color="#151515"/><stop offset="1" stop-color="#262626"/>
      </linearGradient>
      <linearGradient id="lightFade" x1="0" y1="0" x2="0" y2="1">
        <stop offset="0" stop-color="#f7f7f7"/><stop offset="1" stop-color="#e9e9e9"/>
      </linearGradient>
    </defs>
    <rect width="960" height="620" fill="url(#lightFade)"/>
    <polygon points="0,0 960,0 960,598 750,427 650,577 310,577 210,427 0,598" fill="url(#engineTone)" role="img" aria-label="Dark photo of gearbox and engine parts"/>
    <polygon points="0,105 210,427 0,598" fill="#0b0b0b"/>
    <polygon points="960,105 750,427 960,598" fill="#0b0b0b"/>
    <polygon points="0,60 0,105 210,427 236,416" fill="#ffffff"/>
    <polygon points="960,60 960,105 750,427 724,416" fill="#ffffff"/>
    <polygon points="0,0 960,0 960,20 650,577 327,577 0,20" fill="#f7d600" opacity=".95"/>
    <polygon points="75,0 885,0 560,470 400,470" fill="url(#engineTone)" role="img" aria-label="Dark photo of gearbox and engine parts"/>
  </svg>

  <div class="abs brand">
    <span class="brand-mark"></span>
    <span class="brand-name">KOWHAI BAY GROUP</span>
  </div>
  <h1 class="abs headline headline-top">BRAKE AND CLUTCH</h1>
  <p class="abs headline headline-main">BOOSTERS</p>
  <div class="abs product-hero" role="img" aria-label="Photo of a silver clutch booster unit"></div>

  <div class="abs range-box"></div>
  <div class="abs range-title">
    <svg width="680" height="40" viewBox="0 0 680 40" aria-hidden="true"><polygon points="0,40 28,0 652,0 680,40" fill="#0b0b0b"/></svg>
    <span>SUPPLY, REPAIR AND REBUILD OF BOOSTERS</span>
  </div>
  <div class="abs range-item" style="left:93px"><div class="range-photo" role="img" aria-label="Photo of a truck air booster"></div></div>
  <div class="abs range-item" style="left:252px"><div class="range-photo" role="img" aria-label="Photo of brake master cylinders"></div></div>
  <div class="abs range-item" style="left:411px"><div class="range-photo" role="img" aria-label="Photo of a clutch servo unit"></div></div>
  <div class="abs range-item" style="left:570px"><div class="range-photo" role="img" aria-label="Photo of a remote booster"></div></div>
  <div class="abs range-item" style="left:729px"><div class="range-photo" role="img" aria-label="Photo of a vacuum brake booster"></div></div>

  <h2 class="abs company">KOWHAI BAY GROUP</h2>
  <p class="abs specialty">Experts in Remanufactured Brakes, Hoses and Cables</p>

  <svg width="0" height="0" aria-hidden="true" style="position:absolute">
    <symbol id="gear" viewBox="0 0 52 52">
      <circle cx="26" cy="26" r="21" fill="none" stroke="#0b0b0b" stroke-width="9" stroke-dasharray="7 4.5"/>
      <circle cx="26" cy="26" r="18" fill="#0b0b0b"/>
      <circle cx="26" cy="26" r="11.5" fill="#f7d600"/>
      <circle cx="26" cy="26" r="4.5" fill="#0b0b0b"/>
    </symbol>
  </svg>
  <div class="abs service" style="left:52px;top:936px"><svg><use href="#gear"/></svg>Truck Boosters</div>
  <div class="abs service" style="left:309px;top:936px"><svg><use href="#gear"/></svg>Vacuum Boosters</div>
  <div class="abs service-divider" style="left:52px;top:993px;width:225px"></div>
  <div class="abs service-divider" style="left:309px;top:993px;width:232px"></div>
  <div class="abs service-divider" style="left:292px;top:938px;width:1px;height:112px"></div>
  <div class="abs service" style="left:52px;top:998px"><svg><use href="#gear"/></svg>Clutch Boosters</div>
  <div class="abs service" style="left:309px;top:998px"><svg><use href="#gear"/></svg>Remote Boosters</div>
  <p class="abs note">We also stock spare parts, seal kits and repair kits</p>

  <div class="abs aim"></div>
  <svg class="abs" style="left:715px;top:862px" width="94" height="72" viewBox="0 0 94 72" aria-hidden="true">
    <circle cx="40" cy="40" r="30" fill="#f39a1e"/>
    <circle cx="40" cy="40" r="22" fill="#ffffff"/>
    <circle cx="40" cy="40" r="15" fill="#f39a1e"/>
    <circle cx="40" cy="40" r="7" fill="#ffffff"/>
    <line x1="40" y1="40" x2="84" y2="8" stroke="#f39a1e" stroke-width="3"/>
    <polygon points="84,8 76,8 84,1" fill="#f39a1e"/>
  </svg>
  <p class="abs aim-band">OUR PROMISE</p>
  <p class="abs aim-text">Quality rebuilds done<br>right, with the<br>fastest turnaround<br>we can deliver</p>

  <svg class="footer-art" viewBox="0 0 960 128" aria-hidden="true">
    <rect width="960" height="128" fill="#f7d600"/>
    <polygon points="370,34 960,34 960,128 427,128" fill="#0b0b0b"/>
  </svg>
  <div class="abs free-phone"><span class="free-label">FREE PHONE</span><span class="free-number">0800 55 12 80</span></div>
  <div class="abs phones">
    <span><svg width="20" height="20" viewBox="0 0 24 24" aria-hidden="true"><path d="M6.6 10.8a15.2 15.2 0 0 0 6.6 6.6l2.2-2.2c.3-.3.7-.4 1-.2 1.1.4 2.3.6 3.6.6.6 0 1 .4 1 1V20c0 .6-.4 1-1 1A17 17 0 0 1 3 4c0-.6.4-1 1-1h3.5c.6 0 1 .4 1 1 0 1.3.2 2.5.6 3.6.1.3 0 .7-.2 1z" fill="#0b0b0b"/></svg>07 555 0142</span>
    <span><svg width="20" height="20" viewBox="0 0 24 24" aria-hidden="true"><rect x="3" y="9" width="18" height="12" rx="1.5" fill="#0b0b0b"/><rect x="7" y="3" width="10" height="7" fill="#0b0b0b"/><rect x="6" y="12" width="12" height="1.6" fill="#f7d600"/><rect x="6" y="15.5" width="12" height="1.6" fill="#f7d600"/></svg>07 555 0143</span>
  </div>
  <div class="abs contact" style="left:384px;top:1121px">
    <span><svg width="16" height="12" viewBox="0 0 16 12" aria-hidden="true"><rect x=".5" y=".5" width="15" height="11" fill="none" stroke="#0b0b0b"/><path d="M.5 .5 8 7l7.5-6.5" fill="none" stroke="#0b0b0b"/></svg>parts@kowhaibaygroup.co.nz</span>
  </div>
  <div class="abs contact" style="left:664px;top:1121px">
    <span><svg width="15" height="15" viewBox="0 0 16 16" aria-hidden="true"><circle cx="8" cy="8" r="7" fill="none" stroke="#0b0b0b" stroke-width="1.5"/><ellipse cx="8" cy="8" rx="3" ry="7" fill="none" stroke="#0b0b0b" stroke-width="1.2"/><line x1="1" y1="8" x2="15" y2="8" stroke="#0b0b0b" stroke-width="1.2"/></svg>www.kowhaibaygroup.co.nz</span>
  </div>
  <div class="abs address">
    <svg width="16" height="20" viewBox="0 0 16 20" aria-hidden="true"><path d="M8 1a6 6 0 0 0-6 6c0 4.5 6 11 6 11s6-6.5 6-11a6 6 0 0 0-6-6z" fill="#f7d600"/><circle cx="8" cy="7" r="2.3" fill="#0b0b0b"/></svg>
    <span>Kowhai Bay Group<br>18 Bay Road Tauranga</span>
  </div>
  <p class="abs unsubscribe">unsubscribe from this list</p>
</main>
</body>
</html>
```